Family business needs stationery redesign with new logo

Family owned company, established in 1987 wanting a brand 'refresh'. We are an electrical, refrigeration and construction company based in the Barkly Region Northern Territory, Australia. We have a new logo we would like to use which is uploaded along with our current letterhead and email signature. We are also dropping the word 'contractors' so please do not include this on any designs. Please note also, the 'orange' color used in our logo and designs should be Northern Territory red ochre which is as follows:

RGB (Hex): #C75B12
PantoneĀ® 159 C
CMYK: 1 / 74 / 100 / 7

We are needing our stationery redesigned using our new logo. Please include letterheads, business cards, envelopes, and email signatures.

We currently use our business letterheads for quotations, invoices, letters, HR matters, and internal memos.

We also need a separate simplified letterhead for internal paperwork such as employee leave forms, meeting agendas, and meeting minutes etc.

Reason: Needing more submissions of full package designs. We are wanting all our stationery, including business cards, letterheads, email signatures, envelopes, etc to be cohesive. We also require ALL the information, as supplied on our template letterhead, to be included on the new letterhead designs. including electrical license no.etc Thank you, R&W

Reason: needing more time as work has got in the way of looking over designs. A lot of designs not meeting the brief/criteria.

Industry/Entity Type

Business

Colors
0355a3
f37122

Requirements
Must have
• The 'orange' color used in the designs should be Northern Territory red ochre which is as follows:
• RGB (Hex): #C75B12
• PantoneĀ® 159 C
• CMYK: 1 / 74 / 100 / 7
• ***MUST INCLUDE ALL INFORMATION THAT IS ON OUR CURRENT LETTERHEAD***
Should not have
• Please do not include the word 'contractors'

```html
<!DOCTYPE html>
<html lang="en">
<head>
<meta charset="utf-8">
<title>R&amp;W Business Card</title>
<link href="https://fonts.googleapis.com/css2?family=Roboto:wght@400;500;700;900&display=swap" rel="stylesheet">
<style>
  :root {
    --page-bg: #d8d5d1;
    --card-frost: #e9ebed;
    --navy: #1f2a5c;
    --ochre: #c75b12;
    --soft-text: #d3d6e0;
  }
  * { margin: 0; padding: 0; box-sizing: border-box; }
  html, body { width: 1200px; height: 969px; overflow: hidden; }
  body {
    background: var(--page-bg);
    font-family: "Roboto", Arial, sans-serif;
    position: relative;
  }
  .business-card {
    position: absolute;
    left: 100px;
    top: 200px;
    width: 1000px;
    height: 568px;
    border-radius: 26px;
    overflow: hidden;
    background: var(--card-frost);
    box-shadow: 0 10px 30px rgba(0,0,0,0.18);
  }
  .card-band { position: absolute; left: 0; top: 0; width: 1000px; height: 568px; }
  .brand-name {
    position: absolute;
    left: 0; width: 100%;
    top: 70px;
    text-align: center;
    font-weight: 900;
    font-size: 136px;
    line-height: 1;
    color: var(--navy);
    letter-spacing: 2px;
  }
  .person {
    position: absolute;
    left: 57px;
    top: 385px;
    color: var(--soft-text);
  }
  .person-name {
    color: var(--ochre);
    font-weight: 700;
    font-size: 33px;
    letter-spacing: 1px;
    line-height: 40px;
  }
  .person-title { font-size: 27px; line-height: 40px; }
  .person-address { font-size: 26px; line-height: 38px; }
  .contact-list {
    position: absolute;
    right: 42px;
    top: 382px;
    list-style: none;
    color: var(--soft-text);
    font-size: 25px;
  }
  .contact-list li {
    display: flex;
    align-items: center;
    justify-content: flex-end;
    height: 38.5px;
    gap: 22px;
  }
  .contact-icon { width: 24px; height: 24px; flex: none; }
</style>
</head>
<body>
  <div class="business-card">
    <svg class="card-band" viewBox="0 0 1000 568" aria-hidden="true">
      <path d="M0 356 Q500 278 1000 356 L1000 364 Q500 286 0 364 Z" fill="var(--ochre)"/>
      <path d="M0 366 Q500 288 1000 366 L1000 568 L0 568 Z" fill="var(--navy)"/>
    </svg>

    <div class="brand-name">R&amp;W</div>

    <div class="person">
      <p class="person-name">DANIEL HARPER</p>
      <p class="person-title">CEO/Founder</p>
      <p class="person-address">214 Wattle Street</p>
      <p class="person-address">Tennant Creek, NT 0860</p>
    </div>

    <ul class="contact-list">
      <li>612 508 3174
        <svg class="contact-icon" viewBox="0 0 24 24"><path fill="var(--ochre)" d="M6.6 10.8a15.2 15.2 0 0 0 6.6 6.6l2.2-2.2a1 1 0 0 1 1-.25 11.4 11.4 0 0 0 3.6.57 1 1 0 0 1 1 1V20a1 1 0 0 1-1 1A17 17 0 0 1 3 4a1 1 0 0 1 1-1h3.5a1 1 0 0 1 1 1c0 1.25.2 2.45.57 3.57a1 1 0 0 1-.25 1z"/></svg>
      </li>
      <li>437 215 6083
        <svg class="contact-icon" viewBox="0 0 24 24"><g fill="var(--ochre)"><rect x="6" y="3" width="12" height="5"/><rect x="2" y="9" width="20" height="8" rx="1.5"/><rect x="6" y="15" width="12" height="6"/></g><rect x="8" y="17" width="8" height="1.5" fill="var(--navy)"/></svg>
      </li>
      <li>hello@rwservices.com
        <svg class="contact-icon" viewBox="0 0 24 24"><rect x="2" y="5" width="20" height="14" fill="var(--ochre)"/><path d="M2 5 L12 13 L22 5" fill="none" stroke="var(--navy)" stroke-width="1.6"/></svg>
      </li>
      <li>www.rwservices.com
        <svg class="contact-icon" viewBox="0 0 24 24"><circle cx="12" cy="12" r="10" fill="var(--ochre)"/><g fill="none" stroke="var(--navy)" stroke-width="1.4"><ellipse cx="12" cy="12" rx="4" ry="10"/><path d="M2 12h20M4 7h16M4 17h16"/></g></svg>
      </li>
    </ul>
  </div>
</body>
</html>
```